Creation of a construction/bricklaying business website

Following the template format of "Halloway 7", the following content would need to be included:
1. Landing page with 3 tiles that go to their own pages.
- Landing page to include background photo and description of services offered.
2. 3 tiles to include:
a) "Contact Us For A Free Quote or Friendly Discussion" Form (middle tile)
b) Case Studies and Testimonials
c) Certifications and Professional Membership
- Design logo to be used from previous SketchNestle project. Example of logo attached below, please access full JPG files from our account.

Target Market(s)

Prospective clients seeking construction work (bricklaying speciality)

Industry/Entity Type

Residential Construction

Coding

Coded - Design and coding required

Number of Pages Required

4 page

Font styles to use
Sans Serif

Colors

Designer to choose colors to be used in the design.

Requirements
Must have
• Following the template format of "Halloway 7", the following content would need to be included:
• 1. Landing parent page with 3 tiles that go to the 3 child pages.
• - Landing page to include background photo and description of services offered.
• 2. 3 tiles to include:
• a) "Contact Us For A Free Quote or Friendly Discussion" Form (middle tile)
• b) Case Studies and Testimonials (first tile / left side)
• c) Certifications and Professional Memberships (third tile / right side) (This should include logos of the relevant organisations being displayed. Specifically GQT and the Pillar Seal GQT).
• - Design logo to be used from previous SketchNestle project. Example of logo attached below, please access full JPG files from our account.
Nice to have
• Sleek and modern feel.
• Approachable in terms of how people can contact the company for a quote.
• Traditional pictures to give credibility and comfort around choosing this company.
Should not have
• Cheesy pictures
• Over-complicated
• Simple to use
• Easy URL domain name

```html
<!DOCTYPE html>
<html lang="en">
<head>
<meta charset="utf-8">
<title>R.T.Marlow Construction Ltd</title>
<link rel="stylesheet" href="https://fonts.googleapis.com/css2?family=Montserrat:wght@500;600&family=Arimo:wght@400&display=swap">
<style>
:root{
  --blue:#133f94;
  --blue-dark:#0e3378;
  --grey-icon:#444548;
  --text:#4a4a4a;
  --page:#f4f4f4;
  --white:#ffffff;
  --card-border:#dcdcdc;
  --badge-red:#b3122b;
}
*{margin:0;padding:0;box-sizing:border-box}
html,body{width:755px;height:1200px;overflow:hidden}
body{position:relative;background:var(--page);font-family:"Arimo",Arial,sans-serif;color:var(--text)}
.site-header{position:absolute;top:0;left:0;width:755px;height:64px;background:var(--white);border-top:2px solid var(--blue-dark)}
.brand{position:absolute;left:55px;top:17px;font-family:"Montserrat",sans-serif;font-weight:600;font-size:21px;color:var(--blue);line-height:1;display:flex;align-items:center;gap:7px}
.brand-mark{width:12px;height:12px;background:var(--blue)}
.menu-toggle{position:absolute;left:664px;top:15px;width:36px;height:36px;border:1.5px solid #9a9a9a;border-radius:50%;display:flex;align-items:center;justify-content:center}
.hero{position:absolute;top:64px;left:0;width:755px;height:426px;background:linear-gradient(180deg,#2a2a30 0%,#6b4a2a 35%,#8a6a45 55%,#4a3a2c 100%)}
.hero-title{position:absolute;top:215px;left:50%;transform:translateX(-50%);white-space:nowrap;padding:0 11px;height:37px;background:rgba(40,55,90,.55);color:var(--white);font-family:"Montserrat",sans-serif;font-weight:500;font-size:22px;text-align:center;line-height:37px}
.hero-sub{position:absolute;top:262px;left:50%;transform:translateX(-50%);white-space:nowrap;padding:0 14px;height:36px;background:rgba(30,30,30,.35);color:var(--white);font-family:"Montserrat",sans-serif;font-weight:500;font-size:13.5px;text-align:center;line-height:36px}
.hero-edge{position:absolute;top:400px;left:0}
.intro{position:absolute;top:520px;left:0;width:755px;text-align:center;font-family:"Montserrat",sans-serif;font-weight:500;font-size:12px;line-height:22px;color:var(--blue);text-transform:uppercase}
.service{position:absolute;width:160px;text-align:center;font-family:"Montserrat",sans-serif;font-weight:500;font-size:9px;color:var(--text);text-transform:uppercase}
.service .icon{width:72px;height:72px;border-radius:50%;background:var(--grey-icon);margin:0 auto 12px;display:flex;align-items:center;justify-content:center}
.service.active .icon{background:var(--blue)}
.service.active{color:var(--blue)}
.about{position:absolute;top:856px;left:140px;width:475px;text-align:center;font-size:8px;line-height:19px}
.tiles{position:absolute;top:950px;left:54px;display:flex;gap:11px}
.tile{width:209px;height:175px;background:var(--white);border:1px solid var(--card-border);text-align:center;padding:22px 10px 0;position:relative}
.tile h2{font-family:"Montserrat",sans-serif;font-weight:500;font-size:10.5px;line-height:19px;color:var(--blue);text-transform:uppercase;margin-bottom:6px;white-space:nowrap}
.tile p{font-size:8px;line-height:16.5px;padding:0 8px}
.tile p.quote{padding:0 6px}
.btn{position:absolute;left:50%;transform:translateX(-50%);bottom:18px;background:var(--blue);color:var(--white);font-family:"Montserrat",sans-serif;font-weight:500;font-size:8px;width:60px;height:21px;line-height:21px;text-transform:uppercase}
.badges{display:flex;justify-content:center;align-items:center;gap:16px;margin-top:6px}
.badge-wide{width:45px;height:24px;background:var(--blue)}
.badge-sq{width:20px;height:30px;background:var(--badge-red)}
.site-footer{position:absolute;top:1162px;left:0;width:755px;height:38px;background:var(--blue-dark);color:var(--white);font-size:8px;text-align:center;line-height:38px}
</style>
</head>
<body>
<header class="site-header">
  <div class="brand"><span class="brand-mark"></span>R.T.Marlow</div>
  <div class="menu-toggle"><svg width="10" height="8" viewBox="0 0 10 8"><rect y="0" width="10" height="1.6" fill="#444"/><rect y="3.2" width="10" height="1.6" fill="#444"/><rect y="6.4" width="10" height="1.6" fill="#444"/></svg></div>
</header>

<section class="hero" role="img" aria-label="Photograph of a construction site at dusk with cranes and rising buildings">
  <h1 class="hero-title">R.T.Marlow Construction Ltd</h1>
  <p class="hero-sub">Sed ut perspiciatis unde omnis iste natus error sit voluptatem</p>
</section>
<svg class="hero-edge" width="755" height="92" viewBox="0 0 755 92">
  <polygon points="0,6 377,80 755,6 755,11 377,88 0,12" fill="var(--blue)"/>
  <polygon points="0,12 377,88 755,11 755,92 0,92" fill="var(--page)"/>
</svg>

<p class="intro">R.T.Marlow Construction Ltd is a construction company that has<br>expertise &amp; experience in the following areas</p>

<div class="service active" style="left:77px;top:593px">
  <div class="icon"><svg width="38" height="38" viewBox="0 0 38 38" fill="none" stroke="#fff" stroke-width="2" stroke-linejoin="round"><path d="M19 3l8 4v8l-8 4-8-4V7z"/><path d="M11 19l8 4v8l-8 4-8-4v-8z"/><path d="M27 19l8 4v8l-8 4-8-4v-8z"/></svg></div>
  Extensions
</div>
<div class="service" style="left:294px;top:593px">
  <div class="icon"><svg width="34" height="36" viewBox="0 0 34 36" fill="#fff"><rect x="6" y="2" width="22" height="32"/><g fill="#444548"><rect x="9" y="6" width="4" height="4"/><rect x="15" y="6" width="4" height="4"/><rect x="21" y="6" width="4" height="4"/><rect x="9" y="13" width="4" height="4"/><rect x="15" y="13" width="4" height="4"/><rect x="21" y="13" width="4" height="4"/><rect x="9" y="20" width="4" height="4"/><rect x="15" y="20" width="4" height="4"/><rect x="21" y="20" width="4" height="4"/><rect x="14" y="27" width="6" height="7"/></g></svg></div>
  New Build / New Houses
</div>
<div class="service" style="left:512px;top:593px">
  <div class="icon"><svg width="50" height="20" viewBox="0 0 50 20"><rect x="1" y="12" width="48" height="6" fill="#fff"/><path d="M1 12l4-9 3 9 4-10 4 10 4-9 3 9 4-10 4 10 4-9 3 9 4-10 3 10" fill="none" stroke="#fff" stroke-width="2"/></svg></div>
  Garden Walls
</div>
<div class="service" style="left:77px;top:723px">
  <div class="icon"><svg width="34" height="34" viewBox="0 0 34 34" fill="none" stroke="#fff" stroke-width="2"><rect x="3" y="3" width="28" height="28"/><rect x="8" y="8" width="18" height="18"/><path d="M12 12h10M12 16h10M12 20h10"/></svg></div>
  Plastering
</div>
<div class="service" style="left:294px;top:723px">
  <div class="icon"><svg width="38" height="34" viewBox="0 0 38 34" fill="none" stroke="#fff" stroke-width="2"><rect x="3" y="14" width="32" height="18"/><path d="M3 20h32M3 26h32M13 14v6M25 14v6M19 20v6M9 26v6M29 26v6"/><path d="M22 10l8-7" stroke-linecap="round"/></svg></div>
  Brickwork
</div>
<div class="service" style="left:512px;top:723px">
  <div class="icon"><svg width="36" height="34" viewBox="0 0 36 34" fill="none" stroke="#fff" stroke-width="2" stroke-linecap="round"><path d="M4 30l12-20"/><path d="M14 30h18l-4-8h-8z" fill="#fff"/></svg></div>
  Groundworks
</div>

<p class="about">We pride ourselves on attention to detail, pride in our completed project and client satisfaction. We believe in full transparency and this is reflected in the jobs we quote for you. We break down each step with both labour and materials cost so you can see exactly what you are paying for.Feel free to get in touch and we can talk through what you are looking to achieve</p>

<div class="tiles">
  <article class="tile">
    <h2>Case Studies &amp; Testimonials</h2>
    <p class="quote">&ldquo; Sed ut perspiciatis unde omnis iste natus error sit voluptatem accusantium doloremque laudantium to tam rem aperiam, eaque ipsa quae ab illo inventore beatae vitae dicta sunt explicabo. &rdquo;</p>
    <span class="btn">Read More</span>
  </article>
  <article class="tile">
    <h2>Contact us for a free quote<br>or friendly discussion</h2>
    <p>Sed ut perspiciatis unde omnis iste natus error sit voluptatem accusantium doloremque laudantium to beatae vitae dicta sunt explicabo.</p>
    <span class="btn">Read More</span>
  </article>
  <article class="tile">
    <h2>Certifications &amp;Professional<br>Memberships</h2>
    <p>Sed ut perspiciatis unde omnis iste natus error sit beatae vitae dicta sunt explicabo.</p>
    <div class="badges"><span class="badge-wide" aria-label="Pillar Seal GQT badge"></span><span class="badge-sq" aria-label="GQT badge"></span></div>
    <span class="btn" style="bottom:14px">Read More</span>
  </article>
</div>

<footer class="site-footer">&copy; Copyright-2018 R.T.Marlow Construction Ltd.All rights res</footer>
</body>
</html>
```